Cleaning service website design

We need a new nice web design(logo will be the same) for a new cleaning service Company:

Informations about Company and logo you can take from flyers in attachments.

This is a cleaning service Company which have simple rules and we would like to show that(in checklist form) on website:

- What we do and that we're Cleaning Green

- Why us?

- How much(our pricing is simple)

Also we would like to communicate with clients by some nice/big pictures on website and the most important thing is our phone number and short/fast Brimtallow.

Also there should be some space for description about our Company.

Generally all information on main page can be short: about us, about service(what we do), last reviews, tips (for example: Tip of the week) and other can be some introduction to subpage where will be more information.

There will be few subpages like: About us, About our service, Photos(Before and after), Reviews , Tips, FAQ, Contact, Looking for a Job? - most of them will be just text so you can project just one example.

```html
<!DOCTYPE html>
<html lang="en">
<head>
<meta charset="utf-8">
<title>Tidy Nest House Cleaning</title>
<link href="https://fonts.googleapis.com/css2?family=Cabin:wght@400;500&family=Open+Sans:wght@300;400;600&display=swap" rel="stylesheet">
<style>
:root{
  --green:#6cbf4a;
  --green-light:#8fd070;
  --blue:#0d5aa7;
  --ink:#222;
  --text:#3a3a3a;
  --muted:#666;
  --page:#f2f2f2;
  --panel:#e6e6e6;
  --footer:#2b2b2b;
  --footer-dark:#1d1d1d;
  --white:#fff;
}
*{box-sizing:border-box;margin:0;padding:0}
html,body{width:679px;height:1200px;overflow:hidden}
body{position:relative;background:var(--page);font-family:"Open Sans",sans-serif;color:var(--text);font-size:7px;line-height:1.5}
.abs{position:absolute}
ul{list-style:none}

/* header */
.site-header{left:0;top:0;width:679px;height:68px;background:linear-gradient(#fff,#f4f4f4);border-top:3px solid var(--green)}
.brand{left:88px;top:14px;display:flex;align-items:center;gap:6px}
.brand-mark{width:22px;height:22px;border-radius:50%;background:var(--green)}
.brand-name{font-family:"Cabin",sans-serif;font-size:19px;font-weight:500;color:var(--blue)}
.brand-tag{left:115px;top:42px;font-size:6px;color:var(--blue)}
.main-nav{left:252px;top:0;height:40px;display:flex;font-size:6.3px;font-weight:600;letter-spacing:.2px}
.main-nav a{color:var(--ink);text-decoration:none;padding:0 8px;line-height:40px;text-transform:uppercase}
.main-nav a.active{background:var(--green);color:#fff;padding:0 10px}

/* hero */
.hero{left:3px;top:68px;width:676px;height:285px}
.hero-photo{position:absolute;inset:0;background:linear-gradient(100deg,#6b4a2e 0%,#c99b5e 25%,#f1dcb4 45%,#e3b36d 70%,#b98541 100%)}
.promo{left:359px;top:49px;width:245px;height:113px;background:rgba(255,255,255,.93);font-family:"Cabin",sans-serif;color:#2f2a1f}
.promo > div{position:absolute;left:0;width:100%;text-align:center;white-space:nowrap}
.promo-title{top:10px;font-size:22px;line-height:24px;letter-spacing:2px}
.promo-price{top:33px;font-size:12px;line-height:42px;letter-spacing:1px}
.promo-price b{font-size:40px;font-weight:500;vertical-align:-7px;margin-left:5px}
.promo-note{top:79px;font-size:12px;line-height:14px;letter-spacing:.5px}
.promo-code{top:93px;font-size:9.5px;line-height:11px;letter-spacing:.5px}
.phone-box{left:428px;top:177px;width:179px;height:36px;background:var(--blue);color:#fff;padding:4px 7px}
.phone-box b{display:block;font-size:16px;font-weight:400;line-height:1.1}
.phone-box span{font-size:7px}
.call-btn{left:428px;top:217px;width:118px;height:33px;background:var(--green);border-radius:3px;color:#fff;font-family:"Cabin",sans-serif;font-size:18px;text-align:center;line-height:33px}
.slide-arrow{top:136px;width:25px;height:25px;border-radius:50%;background:#2b2b2b;display:flex;align-items:center;justify-content:center}

/* features */
.feature{top:366px;width:165px;text-align:left}
.feature-icon{display:block;margin:0 auto 3px;width:42px;height:42px}
.feature h2{font-family:"Cabin",sans-serif;font-weight:400;font-size:10.5px;color:#444;text-align:center;margin-bottom:6px;letter-spacing:.3px}
.checklist li{position:relative;padding-left:11px;font-size:6.6px;line-height:10.4px}
.checklist li::before{content:"";position:absolute;left:1px;top:2.5px;width:4px;height:2px;border-left:1.2px solid #333;border-bottom:1.2px solid #333;transform:rotate(-45deg)}
.note{text-align:center;font-size:6.6px;line-height:10.4px}
.read-more{font-size:6.6px;font-style:italic;color:var(--green);text-transform:uppercase;letter-spacing:.3px}
.feature .read-more{display:block;text-align:center;margin-top:3px}

/* section bars */
.bar{background:var(--panel);font-family:"Cabin",sans-serif;color:#333;padding-left:11px}

/* tips */
.tips-bar{left:87px;top:529px;width:505px;height:32px;font-size:11.5px;line-height:32px;letter-spacing:.6px}
.tips-intro{left:87px;top:576px;width:112px;font-size:6.8px;line-height:10.4px;color:var(--ink)}
.tip{top:578px;width:117px;height:141px;background:var(--panel)}
.tip-photo{width:115px;height:115px;margin:1px}
.tip-caption{font-family:"Cabin",sans-serif;font-size:8px;text-align:center;letter-spacing:.6px;line-height:24px;color:#333}

/* about */
.about-bar{left:87px;top:736px;width:332px;height:33px;font-size:14px;line-height:33px}
.testi-bar{left:430px;top:736px;width:162px;height:33px;font-size:14px;line-height:33px}
.testi-arrows{right:7px;top:11px;display:flex;gap:1px}
.testi-arrows span{width:12px;height:12px;background:#999;border-radius:2px}
.about-nav{left:87px;top:780px;width:76px}
.about-nav li{position:relative;height:21px;line-height:21px;border-bottom:1px solid #d4d4d4;font-family:"Cabin",sans-serif;font-size:7.5px;color:#444;padding-left:1px}
.about-nav li.active{color:var(--green)}
.about-nav li i{position:absolute;right:0;top:6px;width:8px;height:8px;border-radius:50%;background:#888}
.about-nav li.active i{background:var(--blue)}
.about-text{left:172px;top:781px;width:245px;font-size:6.9px;line-height:10.4px;color:var(--ink)}
.about-text p+p{margin-top:10px}
.quote{left:430px;top:784px;width:162px;height:66px;background:#e9e9e9;padding:6px 8px 0 24px;font-size:6.2px;font-style:italic;line-height:8px;color:#555}
.quote-mark{left:9px;top:6px;font-size:14px;font-weight:600;color:#777;line-height:1;font-style:normal}
.quote-lead{margin-bottom:3px}
.quote-author{left:484px;top:872px;font-size:6.6px;font-style:italic;color:var(--blue)}
.avatar{left:554px;top:863px;width:34px;height:25px;border:1px solid #bbb;background:linear-gradient(#7c8fa8,#3e4e66)}

/* cards */
.card-photo{top:906px;width:160px;height:100px;border:2px solid #ddd;background:#fff}
.card-photo > div{width:100%;height:100%}
.estimate-art{position:relative;background:var(--green)}
.estimate-art .figure{position:absolute;left:8px;top:8px;width:38px;height:82px;background:#a9db93;border-radius:4px}
.estimate-art p{position:absolute;right:6px;top:37px;font-family:"Cabin",sans-serif;font-size:13px;line-height:15px;color:#fff;text-align:right}
.estimate-art p span{color:var(--blue)}
.ba{position:relative;display:flex}
.ba div{flex:1}
.ba .before{background:linear-gradient(#9a8a76,#5f4e3c)}
.ba .after{background:linear-gradient(#e9e4da,#b29a7a);border-left:2px solid var(--green)}
.ba b{position:absolute;top:14px;font-family:"Cabin",sans-serif;font-weight:400;font-size:8.5px;color:var(--blue)}
.card-title{top:1020px;font-family:"Cabin",sans-serif;font-size:9.7px;letter-spacing:.5px;color:#333}
.card-text{top:1036px;width:160px;font-size:6.7px;line-height:10.4px;color:var(--ink)}
.card-more{top:1079px}

/* footer */
.site-footer{left:0;top:1103px;width:679px;height:63px;background:var(--footer)}
.footer-notch{left:330px;top:1103px;width:0;height:0;border-left:10px solid transparent;border-right:10px solid transparent;border-top:8px solid var(--page)}
.footer-title{left:87px;top:1117px;font-family:"Cabin",sans-serif;font-size:10.5px;color:#fff;letter-spacing:.6px}
.footer-text{left:87px;top:1134px;width:180px;font-size:6.8px;line-height:10px;color:#aaa}
.contact-line{left:289px;font-size:6px;color:#ddd;display:flex;align-items:center;gap:5px;font-weight:600}
.bottom-bar{left:0;top:1166px;width:679px;height:34px;background:var(--footer-dark);border-top:1px solid #3a3a3a}
.copyright{left:87px;top:1180px;font-size:6.6px;color:#ccc}
.social{top:1176px;width:19px;height:19px;border-radius:50%;background:#d9d9d9}
</style>
</head>
<body>

<header class="site-header abs">
  <div class="brand abs"><span class="brand-mark"></span><span class="brand-name">Tidy Nest</span></div>
  <div class="brand-tag abs">house cleaning</div>
  <nav class="main-nav abs">
    <a class="active">Home</a><a>About us</a><a>Services</a><a>Gallery</a><a>Tips</a><a>Looking for a job</a><a>FAQ</a><a>Reviews</a><a>Contact</a>
  </nav>
</header>

<section class="hero abs">
  <div class="hero-photo" role="img" aria-label="Bright, tidy bedroom with a low wooden bed and cream bedding"></div>
  <div class="promo abs">
    <div class="promo-title">HOUSE CLEANING</div>
    <div class="promo-price">AS LOW AS<b>$79</b></div>
    <div class="promo-note">*rates are for regular service*</div>
    <div class="promo-code">PROMO:TNHC13</div>
  </div>
  <div class="phone-box abs"><b>555-014-2278</b><span>www.TidyNestHome.ca</span></div>
  <div class="call-btn abs">Call Today!</div>
  <div class="slide-arrow abs" style="left:7px"><svg width="9" height="11" viewBox="0 0 9 11"><path d="M7 1 2 5.5 7 10" fill="none" stroke="#fff" stroke-width="2"/></svg></div>
  <div class="slide-arrow abs" style="left:640px"><svg width="9" height="11" viewBox="0 0 9 11"><path d="M2 1 7 5.5 2 10" fill="none" stroke="#fff" stroke-width="2"/></svg></div>
</section>

<section class="feature abs" style="left:95px">
  <div class="feature-icon" role="img" aria-label="Icon of a cleaner with a vacuum" style="background:#cfcfcf;border-radius:50%"></div>
  <h2>WHAT WE DO</h2>
  <ul class="checklist">
    <li>Thoroughly clean your bathrooms, kitchen, bedrooms and living areas</li>
    <li>Mop or vacuum your floors</li>
    <li>Dust surfaces</li>
    <li>Collect garbage</li>
    <li>Make beds</li>
  </ul>
  <span class="read-more">Read more &gt;</span>
</section>

<section class="feature abs" style="left:270px;width:120px">
  <svg class="feature-icon" viewBox="0 0 42 42" aria-hidden="true"><circle cx="21" cy="21" r="18.5" fill="none" stroke="#555" stroke-width="3"/><path d="M15 16.5a6 6 0 1 1 8.5 5.4c-1.8.9-2.5 1.8-2.5 3.6v1.5" fill="none" stroke="#555" stroke-width="3"/><circle cx="21" cy="31" r="2" fill="#555"/></svg>
  <h2>WHY  US</h2>
  <ul class="checklist">
    <li>Locally Owned &amp; Operated</li>
    <li>Reliable &amp; Affordable</li>
    <li>All Supplies Provided</li>
    <li>Green Cleaning</li>
    <li>Pet Friendly</li>
    <li>No Contracts</li>
  </ul>
  <span class="read-more">Read more &gt;</span>
</section>

<section class="feature abs" style="left:440px;width:135px">
  <svg class="feature-icon" viewBox="0 0 42 42" aria-hidden="true"><path d="M15 5h12l-3 6h-6z" fill="#555"/><path d="M18 12h6c8 4 12 11 12 18 0 6-4 9-15 9S6 36 6 30c0-7 4-14 12-18z" fill="#555"/><text x="21" y="32" text-anchor="middle" font-family="Open Sans,sans-serif" font-size="15" font-weight="600" fill="#fff">$</text></svg>
  <h2>HOW MUCH</h2>
  <ul class="checklist">
    <li>$79 for homes less than 1000 sq ft</li>
    <li>$89 for homes 1000-1800 sq ft</li>
    <li>$99 for homes 1800-2600 sq ft</li>
  </ul>
  <p class="note">*If your home is larger than<br>2600 sq ft please call for a quote.<br>*rates are for regular service*</p>
  <span class="read-more">Read more &gt;</span>
</section>

<h2 class="tips-bar bar abs" style="font-weight:400">TIPS OF THE WEEK</h2>
<div class="tips-intro abs">
  <p>We understand that reliability and thoroughness are what you look for in an affordable, professional house cleaning service. We pay attention to your needs. We get the job done!</p>
  <p class="read-more" style="margin-top:10px">Read more &gt;</p>
</div>
<figure class="tip abs" style="left:215px">
  <div class="tip-photo" role="img" aria-label="Sweeping a wooden floor with a broom" style="background:linear-gradient(#e8d3a0,#b7874a)"></div>
  <figcaption class="tip-caption">Sweeping Solutions</figcaption>
</figure>
<figure class="tip abs" style="left:345px">
  <div class="tip-photo" role="img" aria-label="Wiping down a kitchen counter" style="background:linear-gradient(#d6c08e,#6b5a3e)"></div>
  <figcaption class="tip-caption">In The Kitchen</figcaption>
</figure>
<figure class="tip abs" style="left:473px">
  <div class="tip-photo" role="img" aria-label="Spotless bathtub beside a stone fireplace" style="background:linear-gradient(#5a4433,#c7bdb2)"></div>
  <figcaption class="tip-caption">Bathroom Boosters</figcaption>
</figure>

<h2 class="about-bar bar abs" style="font-weight:400">ABOUT</h2>
<h2 class="testi-bar bar abs" style="font-weight:400">TESTIMONIALS<span class="testi-arrows abs"><span></span><span></span></span></h2>

<ul class="about-nav abs">
  <li class="active">About Us<i></i></li>
  <li>Mission<i></i></li>
  <li>Vision<i></i></li>
</ul>
<div class="about-text abs">
  <p>Have you ever wondered what it would be like if your life was simpler? We're here to help you get there by taking over the chore of house cleaning. With our help you'll have more time to spend on the things that matter most to you.</p>
  <p>With Tidy Nest you not only get a professional service, but you get it at an affordable price. The owner makes it apoint to be at each and every cleaning to assure your needs are met.</p>
</div>

<blockquote class="quote abs">
  <span class="quote-mark abs">&ldquo;</span>
  <p class="quote-lead">It's about caring, not just cleaning.</p>
  <p>Having personally experienced the struggles of finding quality maid service for our home, we want to make it simpler for families in the Lakeview area.</p>
</blockquote>
<div class="quote-author abs">- Clara &amp; Devin</div>
<div class="avatar abs" role="img" aria-label="Portrait photo of the reviewers"></div>

<div class="card-photo abs" style="left:87px"><div role="img" aria-label="Group of seniors enjoying a day on the golf course" style="background:linear-gradient(#dfe9d2,#8fae6a)"></div></div>
<div class="card-photo abs" style="left:259px"><div class="estimate-art"><div class="figure" role="img" aria-label="Smiling cleaner with a vacuum"></div><p><span>SHORT &amp; FAST</span><br>BRIMTALLOW</p></div></div>
<div class="card-photo abs" style="left:431px"><div class="ba" role="img" aria-label="Cluttered room before cleaning beside the same room after cleaning"><div class="before"></div><div class="after"></div><b style="left:16px">BEFORE</b><b style="left:110px">AFTER</b></div></div>

<h3 class="card-title abs" style="left:87px;font-weight:400">Rules</h3>
<ul class="checklist card-text abs" style="left:87px">
  <li>Rule1- Lorem Ipsum is simply dummy</li>
  <li>Rule2- Lorem Ipsum is simply dummy</li>
  <li>Rule3- Lorem Ipsum is simply dummy</li>
</ul>
<span class="read-more card-more abs" style="left:137px">Read more &gt;</span>

<h3 class="card-title abs" style="left:259px;font-weight:400">Short &amp; Fast Brimtallow</h3>
<p class="card-text abs" style="left:259px">Lorem Ipsum is simply dummy text of the printing and typesetting industry. Lorem Ipsum has been the industry's standard</p>
<span class="read-more card-more abs" style="left:314px">Read more &gt;</span>

<h3 class="card-title abs" style="left:431px;font-weight:400">Before &amp; After Reviews</h3>
<p class="card-text abs" style="left:431px">Lorem Ipsum is simply dummy text of the printing and typesetting industry. Lorem Ipsum has been the industry's standard</p>
<span class="read-more card-more abs" style="left:479px">Read more &gt;</span>

<footer>
  <div class="site-footer abs"></div>
  <div class="footer-notch abs"></div>
  <h2 class="footer-title abs" style="font-weight:400">CONTACT INFO</h2>
  <p class="footer-text abs">Lorem Ipsum is simply dummy text of the printing and typesetting industry.</p>
  <div class="contact-line abs" style="top:1137px">
    <svg width="9" height="9" viewBox="0 0 9 9"><rect width="9" height="9" rx="1" fill="#ddd"/><path d="M2.5 2c.5 2.5 2 4 4.5 4.8l.5-1.2-1.3-.6-.6.6C4.7 5 4 4.3 3.5 3.4l.6-.6-.6-1.3z" fill="#2b2b2b"/></svg>
    PHONE : 555-014-2278
  </div>
  <div class="contact-line abs" style="top:1151px">
    <svg width="9" height="7" viewBox="0 0 9 7"><rect width="9" height="7" fill="#ddd"/><path d="M0 0 4.5 4 9 0" fill="none" stroke="#2b2b2b" stroke-width="1"/></svg>
    EMAIL  : www.TidyNestHome.ca
  </div>
  <div class="bottom-bar abs"></div>
  <p class="copyright abs">Copyright &copy; 2013 TidyNestHome All Rights Reserved.</p>
  <span class="social abs" style="left:501px"></span>
  <span class="social abs" style="left:525px"></span>
  <span class="social abs" style="left:548px"></span>
  <span class="social abs" style="left:572px"></span>
</footer>

</body>
</html>
```